Tobble *

To create online free mini games website. There’re will be up to 100 games on website with 6-8 categories. Domain name is not selected yet.

Number of Pages Required

1 page

```html
<!DOCTYPE html>
<html lang="en">
<head>
<meta charset="utf-8">
<title>Tobble Games</title>
<link href="https://fonts.googleapis.com/css2?family=Oswald:wght@300;400;500&family=Poppins:wght@400;500;600&display=swap" rel="stylesheet">
<style>
:root{
  --sky:#86cde0;
  --grass:#1f8b36;
  --grass-light:#4fae3c;
  --white:#ffffff;
  --blue:#3a8ee6;
  --blue-dark:#2f7fd6;
  --orange:#f07a22;
  --gold:#f6b320;
  --green:#3aaa35;
  --ink:#444444;
  --line:#dddddd;
  --tab-grey:#d4d4d4;
  --black:#0b0b0b;
  --star:#f07a22;
}
*{box-sizing:border-box;margin:0;padding:0}
html,body{width:1200px;height:2267px;overflow:hidden}
body{font-family:'Poppins',sans-serif;color:var(--ink);
  background:linear-gradient(180deg,var(--sky) 0,#8fd3e3 650px,var(--grass-light) 700px,#2a9a3a 880px,var(--grass) 1100px,var(--grass) 100%);}
.page{position:relative;width:1200px;height:2267px}
.brand{position:absolute;top:58px;left:0;width:1200px;text-align:center;font-family:'Oswald',sans-serif;font-weight:500;font-size:50px;letter-spacing:2px;color:#5a8a2a}
.board{position:absolute;left:110px;top:183px;width:981px;height:1641px;background:var(--white);box-shadow:0 4px 14px rgba(0,0,0,.25)}
.hero{position:absolute;left:21px;top:21px;width:937px;height:468px;
  background:linear-gradient(180deg,#4796ee 0,#4a9bf0 40%,#5aa8f2 62%,#86d4f0 62%,#9adcf2 70%,#ffffff 70%,#ffffff 71.5%,#6cc24a 71.5%,#3f9a33 77%,#2f6e2a 81%,#3a2f2c 84%,#2a2634 90%,#232030 100%)}
.hero-title{position:absolute;top:122px;left:0;width:100%;text-align:center;font-family:'Oswald',sans-serif;font-weight:400;font-size:62px;color:var(--white);letter-spacing:1px}
.hero-btn{position:absolute;top:213px;left:400px;width:136px;height:34px;border-radius:17px;background:var(--gold);color:var(--white);font-size:14px;font-weight:600;text-align:center;line-height:34px;letter-spacing:1px}
.nav{position:absolute;left:21px;top:489px;width:937px;height:54px;background:var(--blue);border-bottom:4px solid #5fb0f5;display:flex;align-items:center}
.nav a{color:var(--white);text-decoration:none;font-size:14px;font-weight:500;padding:0 15px;height:50px;line-height:50px;border-right:1px solid var(--blue-dark)}
.search{margin-left:auto;margin-right:14px;width:204px;height:27px;border-radius:14px;background:var(--white);font-size:10px;color:#888;padding-left:12px;line-height:27px;position:relative}
.search svg{position:absolute;right:12px;top:8px}
.heading{position:absolute;left:21px;width:685px;height:39px;border-bottom:2px solid #e4e4e4}
.heading span{display:block;width:133px;height:39px;background:var(--blue);color:var(--white);font-family:'Oswald',sans-serif;font-weight:400;font-size:15px;line-height:39px;padding-left:14px;clip-path:polygon(0 0,88% 0,100% 100%,0 100%)}
.cats{position:absolute;left:21px;top:1287px;width:685px;height:41px;border-bottom:2px solid #e4e4e4;display:flex;gap:2px}
.cats span{display:block;height:39px;background:var(--tab-grey);color:#555;font-family:'Oswald',sans-serif;font-weight:300;font-size:15px;line-height:39px;padding-left:14px;clip-path:polygon(0 0,84% 0,100% 100%,0 100%)}
.cats .on{background:var(--blue);color:var(--white);font-weight:400}
.grid{position:absolute;left:21px;width:685px;display:flex;gap:20px}
.card{width:156px;height:216px;border:1px solid var(--line);text-align:center}
.card .thumb{height:142px}
.card p{font-family:'Oswald',sans-serif;font-weight:300;font-size:14px;color:var(--ink);margin-top:14px}
.stars{color:var(--star);font-size:12px;letter-spacing:1px;margin-top:2px}
.side{position:absolute;left:757px;width:200px}
.widget-head{height:47px;color:var(--white);font-family:'Oswald',sans-serif;font-weight:400;font-size:20px;line-height:47px;padding-left:12px}
.recent{display:flex;height:88px;border:1px solid #e8e8e8;margin-bottom:16px}
.recent .thumb{width:93px;height:86px}
.recent div.txt{padding:10px 0 0 10px;font-family:'Oswald',sans-serif;font-weight:300;font-size:13px;line-height:21px;color:var(--ink)}
.recent .stars{font-size:10px;margin-top:4px}
.tags{display:flex;flex-wrap:wrap;gap:12px 5px;margin-top:16px}
.tags span{height:27px;border:1px solid #999;font-size:12px;line-height:25px;text-align:center;color:#555}
.footer{position:absolute;top:1890px;left:0;width:1200px}
.fcol{position:absolute;top:0;color:var(--white)}
.fcol h3{font-family:'Oswald',sans-serif;font-weight:400;font-size:22px;text-transform:uppercase;margin-bottom:18px}
.news p{font-size:11px;line-height:18px;width:280px}
.signup{display:flex;margin-top:18px;height:39px}
.signup .email{width:157px;background:var(--white);color:#555;font-size:11px;line-height:39px;padding-left:12px}
.signup .go{width:115px;background:var(--orange);font-size:12px;font-weight:600;line-height:37px;text-align:center;border:1px solid var(--white)}
.social{display:flex;gap:5px;margin-top:18px}
.social span{width:27px;height:27px;border:1px solid var(--white);border-radius:50%;position:relative}
.social span::after{content:"";position:absolute;left:9px;top:9px;width:7px;height:7px;border-radius:50%;background:var(--white)}
.contact li{list-style:none;position:relative;padding-left:24px;font-size:12px;line-height:19.5px;margin-bottom:10px}
.contact svg{position:absolute;left:0;top:4px}
.post{display:flex;gap:18px;margin-bottom:24px}
.post .thumb{width:86px;height:63px;border:2px solid var(--white)}
.post h4{font-size:15px;font-weight:600;line-height:21px;width:215px}
.post small{display:block;font-size:11px;font-weight:600;margin-top:6px}
.bottom{position:absolute;top:2155px;left:0;width:1200px;height:112px;background:var(--black);color:var(--white);text-align:center;font-size:12px}
.bottom .links{margin-top:30px}
.bottom .copy{margin-top:12px}
</style>
</head>
<body>
<div class="page">
  <div class="brand">TOBBLE GAMES</div>

  <main class="board">
    <div class="hero" role="img" aria-label="Pixel-art game scene with clouds, trees, a player figure, a trophy and gold coins on grass">
      <div class="hero-title">TOBBLE GAMES</div>
      <div class="hero-btn">READ MORE</div>
    </div>

    <nav class="nav">
      <a>ACTION</a><a>CASINO</a><a>ADVENTURE</a><a>PUZZLE</a><a>DRIVING</a><a>SPORTS</a><a>BUBBLE</a>
      <div class="search">Search
        <svg width="10" height="10" viewBox="0 0 10 10"><circle cx="4" cy="4" r="3" fill="none" stroke="#555" stroke-width="1.5"/><line x1="6.3" y1="6.3" x2="9" y2="9" stroke="#555" stroke-width="1.5"/></svg>
      </div>
    </nav>

    <div class="heading" style="top:601px"><span>EDITOR'S PICK</span></div>
    <div class="grid" style="top:668px">
      <div class="card"><div class="thumb" role="img" aria-label="Board game map thumbnail" style="background:linear-gradient(135deg,#d8d48a 0,#b9c86a 40%,#8fae55 75%,#6f9a48 100%)"></div><p>Quis autem vel eum iure</p><div class="stars">☆☆☆☆☆</div></div>
      <div class="card"><div class="thumb" role="img" aria-label="Platform game thumbnail" style="background:linear-gradient(180deg,#3aa0e0 0,#5bb4ea 45%,#6a5a3a 65%,#3a2a1a 100%)"></div><p>Quis autem vel eum iure</p><div class="stars">☆☆☆☆☆</div></div>
      <div class="card"><div class="thumb" role="img" aria-label="Pirate board game thumbnail" style="background:linear-gradient(135deg,#4a9ad8 0,#2a6fb0 40%,#c8a040 70%,#1f3e6a 100%)"></div><p>Quis autem vel eum iure</p><div class="stars">☆☆☆☆☆</div></div>
      <div class="card"><div class="thumb" role="img" aria-label="Maze game thumbnail" style="background:linear-gradient(135deg,#f6d46a 0,#f3c14a 45%,#d8962a 80%,#b8741a 100%)"></div><p>Quis autem vel eum iure</p><div class="stars">☆☆☆☆☆</div></div>
    </div>

    <div class="heading" style="top:937px"><span>HOT GAMES</span></div>
    <div class="grid" style="top:1003px">
      <div class="card"><div class="thumb" role="img" aria-label="Word search game thumbnail" style="background:linear-gradient(135deg,#f2e27a 0,#e8e08a 40%,#7ab85a 70%,#3f8e3a 100%)"></div><p>Quis autem vel eum iure</p><div class="stars">☆☆☆☆☆</div></div>
      <div class="card"><div class="thumb" role="img" aria-label="Roulette wheel thumbnail" style="background:linear-gradient(135deg,#3a2a22 0,#7a4a2a 40%,#2e6b34 70%,#1f4f26 100%)"></div><p>Quis autem vel eum iure</p><div class="stars">☆☆☆☆☆</div></div>
      <div class="card"><div class="thumb" role="img" aria-label="Platform level thumbnail" style="background:linear-gradient(180deg,#8fd0f2 0,#7fc8f0 30%,#4a5a6a 60%,#2a2a3a 100%)"></div><p>Quis autem vel eum iure</p><div class="stars">☆☆☆☆☆</div></div>
      <div class="card"><div class="thumb" role="img" aria-label="Mushroom landscape thumbnail" style="background:linear-gradient(180deg,#3e9ee8 0,#8acdf5 45%,#d8503a 65%,#5db83c 80%,#3f9a2c 100%)"></div><p>Quis autem vel eum iure</p><div class="stars">☆☆☆☆☆</div></div>
    </div>

    <div class="cats"><span class="on" style="width:95px">ACTION</span><span style="width:96px">CASINO</span><span style="width:104px">ADVENTURE</span><span style="width:96px">PUZZLE</span><span style="width:95px">DRIVING</span><span style="width:96px">SPORTS</span><span style="width:95px">BUBBLE</span></div>
    <div class="grid" style="top:1357px">
      <div class="card"><div class="thumb" role="img" aria-label="Treasure crossword thumbnail" style="background:linear-gradient(180deg,#e2f0f8 0,#cfe8f5 40%,#5aaad8 70%,#2a6aa0 100%)"></div><p>Quis autem vel eum iure</p><div class="stars">☆☆☆☆☆</div></div>
      <div class="card"><div class="thumb" role="img" aria-label="Casino table thumbnail" style="background:linear-gradient(135deg,#3f8a44 0,#2f7a3a 50%,#1c4f26 85%,#2a2a2a 100%)"></div><p>Quis autem vel eum iure</p><div class="stars">☆☆☆☆☆</div></div>
      <div class="card"><div class="thumb" role="img" aria-label="Dark platform game thumbnail" style="background:linear-gradient(180deg,#2f5a7e 0,#2a4a6a 45%,#3a6aa0 70%,#1a2a3a 100%)"></div><p>Quis autem vel eum iure</p><div class="stars">☆☆☆☆☆</div></div>
      <div class="card"><div class="thumb" role="img" aria-label="Card table thumbnail" style="background:linear-gradient(135deg,#8a5a3e 0,#6a4a34 35%,#2a7a3a 70%,#1f5a2e 100%)"></div><p>Quis autem vel eum iure</p><div class="stars">☆☆☆☆☆</div></div>
    </div>

    <aside class="side" style="top:612px">
      <div class="widget-head" style="background:var(--orange)">Game of Day</div>
      <div role="img" aria-label="Featured underwater game artwork with play button" style="height:240px;background:linear-gradient(180deg,#6ac4f0 0,#3fa6e6 35%,#2a7ec0 70%,#1b4f7a 100%)"></div>
    </aside>

    <aside class="side" style="top:932px">
      <div class="widget-head" style="background:var(--green)">Recently Visited</div>
      <div style="margin-top:17px">
        <div class="recent"><div class="thumb" role="img" aria-label="Crossword game thumbnail" style="background:linear-gradient(135deg,#e8e8e8,#9aa8b8 60%,#5a6a7a)"></div><div class="txt">Nemo enim ipsam<br>voluptatem quia<div class="stars">★★★☆☆</div></div></div>
        <div class="recent"><div class="thumb" role="img" aria-label="Platform game thumbnail" style="background:linear-gradient(180deg,#4a4a5a,#2a2a34 60%,#1a1a22)"></div><div class="txt">Nemo enim ipsam<br>voluptatem quia<div class="stars">★★★☆☆</div></div></div>
        <div class="recent"><div class="thumb" role="img" aria-label="Space game thumbnail" style="background:linear-gradient(180deg,#1a2a4a,#4a5a7a 55%,#6a5a2a)"></div><div class="txt">Nemo enim ipsam<br>voluptatem quia<div class="stars">★★★☆☆</div></div></div>
      </div>
    </aside>

    <aside class="side" style="top:1331px">
      <div class="widget-head" style="background:var(--green)">Tags</div>
      <div class="tags">
        <span style="width:84px">Action</span><span style="width:100px;margin-left:11px">Adventure</span>
        <span style="width:60px">Puzzle</span><span style="width:59px">Driving</span><span style="width:66px">Sports</span>
        <span style="width:84px">Bubble</span><span style="width:100px;margin-left:11px">Adventure</span>
      </div>
    </aside>
  </main>

  <footer class="footer">
    <div class="fcol news" style="left:131px">
      <h3>Sign up for newsletter</h3>
      <p>Excepteur sint occaecat cupidatat non proident, sunt in culpa qui officia deserunt</p>
      <div class="signup"><div class="email">Enter email</div><div class="go">SUBSCRIPTION</div></div>
      <div class="social"><span></span><span></span><span></span><span></span><span></span></div>
    </div>
    <div class="fcol contact" style="left:491px">
      <h3>Contact Us</h3>
      <ul>
        <li><svg width="11" height="14" viewBox="0 0 11 14"><path d="M5.5 0a5 5 0 0 0-5 5c0 4 5 9 5 9s5-5 5-9a5 5 0 0 0-5-5z" fill="#fff"/><circle cx="5.5" cy="5" r="2" fill="#1f8b36"/></svg>Tobble Games<br>Larchmont Lane 14<br>4100 Verden Eastland</li>
        <li><svg width="12" height="12" viewBox="0 0 12 12"><path d="M2.5 0l2 3-1.3 1.5a7 7 0 0 0 4.3 4.3L9 7.5l3 2-1.5 2.5C5 12 0 7 0 1.5z" fill="#fff"/></svg>Phone: (03) 5550 1234<br>Fax: (03) 5550 1234</li>
        <li><svg width="12" height="9" viewBox="0 0 12 9"><rect width="12" height="9" fill="#fff"/><path d="M0 0l6 5 6-5" fill="none" stroke="#1f8b36" stroke-width="1.2"/></svg>info@tobblegames.example</li>
      </ul>
    </div>
    <div class="fcol" style="left:756px">
      <h3>Latest Posts</h3>
      <div class="post"><div class="thumb" role="img" aria-label="Board game post thumbnail" style="background:linear-gradient(135deg,#e07a3a,#c8a050 45%,#3a9ad0)"></div><div><h4>Nemo enim ipsam voluptatem quia voluptas</h4><small>&#9638; JULY 05, 2018</small></div></div>
      <div class="post"><div class="thumb" role="img" aria-label="Blue puzzle post thumbnail" style="background:linear-gradient(135deg,#5aa0e0,#3a8ad8 45%,#1f5aa0)"></div><div><h4>Nemo enim ipsam voluptatem quia voluptas</h4><small>&#9638; JULY 05, 2018</small></div></div>
    </div>
  </footer>

  <div class="bottom">
    <div class="links">About Us &nbsp;|&nbsp; Contact Us &nbsp;|&nbsp; Terms &amp; Conditions</div>
    <div class="copy">Copyright © Tobble Games 2018. All rights reserved.</div>
  </div>
</div>
</body>
</html>
```